Business card for medical clinic

I need an upmarket, modern medical/health business card for my clinic

Contact Information for Business Card

name, address, email, qr code

```html
<!DOCTYPE html>
<html lang="en">
<head>
<meta charset="UTF-8">
<title>Meridian Care Clinic – Business Card</title>
<link href="https://fonts.googleapis.com/css2?family=Montserrat:wght@400;500;700;800&display=swap" rel="stylesheet">
<style>
  :root{
    --backdrop:#1d1d1f;
    --sky:#29abe2;
    --ocean:#1670a6;
    --navy:#1b3a5c;
    --brand-blue:#1f7fc0;
    --ink:#2a2a2e;
    --paper:#ffffff;
  }
  *{margin:0;padding:0;box-sizing:border-box}
  html,body{width:1200px;height:880px;overflow:hidden;background:var(--backdrop);font-family:'Montserrat',sans-serif}
  .canvas{position:relative;width:1200px;height:880px}
  .card{position:absolute;width:640px;height:366px;border-radius:26px;overflow:hidden}

  /* front */
  .card-front{left:60px;top:56px;background:linear-gradient(160deg,var(--sky) 0%,#2398d4 40%,var(--ocean) 100%)}
  .front-brand{position:absolute;inset:0;display:flex;align-items:center;justify-content:center;gap:18px;padding:0 40px}
  .front-brand .mark{flex:none;width:56px;height:56px;border-radius:50%;background:#1a82bf}
  .front-brand .brand-name{font-weight:700;font-size:28px;letter-spacing:1.5px;color:#1a82bf;text-transform:uppercase;white-space:nowrap}

  /* back */
  .card-back{left:500px;top:460px;background:var(--paper)}
  .back-brand{position:absolute;left:40px;top:36px;display:flex;align-items:center;gap:12px}
  .back-brand .mark{width:30px;height:30px;border-radius:50%;background:var(--navy)}
  .back-brand .brand-name{font-weight:700;font-size:17px;letter-spacing:1px;color:var(--navy);text-transform:uppercase}

  .identity{position:absolute;left:0;top:118px;padding-left:58px}
  .identity .accent-bar{position:absolute;left:26px;top:4px;width:14px;height:50px;background:linear-gradient(180deg,var(--navy),var(--brand-blue))}
  .identity .person{font-weight:800;font-size:28px;color:var(--brand-blue);letter-spacing:.5px;line-height:1.1}
  .identity .role{font-size:16px;color:var(--ink);margin-top:4px}

  .address{position:absolute;left:58px;top:200px;font-size:15px;color:var(--ink);line-height:1.5}
  .contacts{position:absolute;left:58px;top:262px;list-style:none}
  .contacts li{display:flex;align-items:center;gap:10px;font-size:15px;color:var(--ink);line-height:1.65}
  .contacts svg{width:15px;height:15px;fill:var(--brand-blue)}
</style>
</head>
<body>
<main class="canvas">

  <section class="card card-front" aria-label="Card front">
    <div class="front-brand">
      <span class="mark"></span>
      <span class="brand-name">Meridian Care Clinic</span>
    </div>
  </section>

  <section class="card card-back" aria-label="Card back">
    <div class="back-brand">
      <span class="mark"></span>
      <span class="brand-name">Meridian Care Clinic</span>
    </div>

    <div class="identity">
      <span class="accent-bar"></span>
      <h1 class="person">DANIEL HART</h1>
      <p class="role">Managing Director</p>
    </div>

    <p class="address">Your address, City<br>State, Zip 1234</p>

    <ul class="contacts">
      <li>
        <svg viewBox="0 0 24 24" aria-hidden="true"><path d="M6.6 10.8a15.1 15.1 0 0 0 6.6 6.6l2.2-2.2a1 1 0 0 1 1-.25 11.4 11.4 0 0 0 3.6.57 1 1 0 0 1 1 1V20a1 1 0 0 1-1 1A17 17 0 0 1 3 4a1 1 0 0 1 1-1h3.5a1 1 0 0 1 1 1c0 1.25.2 2.450.57 3.57a1 1 0 0 1-.25 1z"/></svg>
        123 456 789
      </li>
      <li>
        <svg viewBox="0 0 24 24" aria-hidden="true"><path d="M3 5h18a1 1 0 0 1 1 1v12a1 1 0 0 1-1 1H3a1 1 0 0 1-1-1V6a1 1 0 0 1 1-1zm9 7.5L20 7H4z"/></svg>
        info@yourmail.com
      </li>
      <li>
        <svg viewBox="0 0 24 24" aria-hidden="true"><path d="M12 2a10 10 0 1 0 0 20 10 10 0 0 0 0-20zm6.9 6h-2.9a15.6 15.6 0 0 0-1.4-3.6A8 8 0 0 1 18.9 8zM12 4a14 14 0 0 1 1.9 4h-3.8A14 14 0 0 1 12 4zM4.3 14a8 8 0 0 1 0-4h3.4a16.5 16.5 0 0 0 0 4zm.8 2h2.9a15.6 15.6 0 0 0 1.4 3.6A8 8 0 0 1 5.1 16zM8 8H5.1a8 8 0 0 1 4.3-3.6A15.6 15.6 0 0 0 8 8zm4 12a14 14 0 0 1-1.9-4h3.8A14 14 0 0 1 12 20zm2.3-6H9.7a14.7 14.7 0 0 1 0-4h4.6a14.7 14.7 0 0 1 0 4zm.3 5.6a15.6 15.6 0 0 0 1.4-3.6h2.9a8 8 0 0 1-4.3 3.6zM16.3 14a16.5 16.5 0 0 0 0-4h3.4a8 8 0 0 1 0 4z"/></svg>
        www.yourwebsite.com
      </li>
    </ul>
  </section>

</main>
</body>
</html>
```